BrimFalcon Business Cards

We have a defined brand. Please visit our website to get a feel for the product and the color pallets. www.brimfalcon-example.com

We need an updated, world class business card design. (See the attached existing card design). Please utilize BOTH sides of the card as shown and be creative with the layout. I do want the horse head icon to be positioned as it is with the existing card.

The remainder of the layout can be customized and I also want it vertically oriented.

Attached are the logo files and please use the colors as follows:
Green - #A5CE39
Tan - #CDBD99
Black

Feel free to play with the colors.

```html
<!DOCTYPE html>
<html lang="en">
<head>
<meta charset="utf-8">
<title>BrimFalcon Business Cards</title>
<link href="https://fonts.googleapis.com/css2?family=Roboto:wght@400;500;700&display=swap" rel="stylesheet">
<style>
  :root {
    --green: #a5ce39;
    --ink: #111111;
    --paper: #ffffff;
    --grey: #444444;
    --stage: #e6e6e4;
  }
  * { margin: 0; padding: 0; box-sizing: border-box; }
  html, body { width: 1200px; height: 1108px; overflow: hidden; }
  body {
    background: var(--stage);
    font-family: "Roboto", Arial, sans-serif;
    display: flex;
    justify-content: center;
    align-items: center;
    gap: 80px;
  }
  .card {
    width: 420px;
    height: 700px;
    border-radius: 26px;
    position: relative;
    overflow: hidden;
    box-shadow: 0 10px 30px rgba(0,0,0,0.15);
  }
  .card-front { background: var(--paper); }
  .card-back { background: var(--green); }

  .front-brand {
    position: absolute;
    top: 150px;
    left: 0; right: 0;
    text-align: center;
  }
  .brand-mark {
    display: block;
    width: 28px; height: 28px;
    border-radius: 50%;
    background: var(--ink);
    margin: 0 auto 18px;
  }
  .brand-name {
    font-weight: 700;
    font-size: 46px;
    color: var(--ink);
    letter-spacing: 0.5px;
  }
  .brand-rule {
    width: 260px;
    height: 1px;
    background: var(--ink);
    margin: 6px auto 8px;
  }
  .tagline {
    font-size: 17px;
    letter-spacing: 7px;
    color: var(--green);
    font-weight: 500;
  }

  .contact {
    position: absolute;
    top: 340px;
    left: 0; right: 0;
    text-align: center;
  }
  .person-name {
    font-weight: 700;
    font-size: 30px;
    color: var(--ink);
  }
  .person-title {
    font-size: 16px;
    color: var(--green);
    margin-top: 2px;
  }
  .contact-rule {
    width: 260px;
    height: 2px;
    background: var(--green);
    margin: 10px auto;
  }
  .contact-line {
    font-size: 14px;
    color: var(--grey);
    line-height: 1.35;
  }
  .address { margin-top: 2px; font-size: 15px; }

  .web-band {
    position: absolute;
    left: 0; right: 0;
    bottom: 70px;
    height: 58px;
    background: var(--green);
    display: flex;
    align-items: center;
    justify-content: center;
    color: var(--paper);
    font-size: 16px;
    font-weight: 500;
    letter-spacing: 1.5px;
  }

  .back-name {
    position: absolute;
    top: 90px;
    left: 0; right: 0;
    text-align: center;
    font-weight: 700;
    font-size: 50px;
    color: var(--ink);
    letter-spacing: 0.5px;
  }
  .back-mark {
    position: absolute;
    left: -90px;
    bottom: -90px;
    width: 380px;
    height: 380px;
    border-radius: 50%;
    background: var(--ink);
  }
</style>
</head>
<body>
  <section class="card card-front">
    <div class="front-brand">
      <span class="brand-mark"></span>
      <div class="brand-name">BrimFalcon</div>
      <div class="brand-rule"></div>
      <div class="tagline">MOTION REDEFINED</div>
    </div>
    <div class="contact">
      <div class="person-name">Daniel Hartwell</div>
      <div class="person-title">President &amp; CEO</div>
      <div class="contact-rule"></div>
      <div class="contact-line">555.010.4817 | daniel@brimfalcon-example.com</div>
      <div class="contact-rule"></div>
      <div class="contact-line address">Harlow Ridge, Saskatchewan,<br>Canada</div>
    </div>
    <div class="web-band">www.brimfalcon-example.com</div>
  </section>

  <section class="card card-back">
    <div class="back-name">BrimFalcon</div>
    <div class="back-mark"></div>
  </section>
</body>
</html>
```